Dental specialist needs a sharp looking letterhead

I am looking for a letterhead to be used to send letters and communication between myself (a dental specialist) and other dentists.
My office is a state of the art dental specialty office.
I need to letterhead to also state:
Bertram L. Oswick DDS
2748 Tollard Avenue, Suite K
West Tollard, NY 14391
(716)392-5061
fax: (716)392-5087
oswickroot.com (**this email address may change)

i included my logo designs.
thank you

Target Market(s)

dentists

Industry/Entity Type

Communication

Requirements
Must have
• the included logo, whether the vertical or horizontal versions

```html
<!DOCTYPE html>
<html lang="en">
<head>
<meta charset="utf-8">
<title>Keystone Endodontics P.C. Letterhead</title>
<link rel="stylesheet" href="https://fonts.googleapis.com/css2?family=Merriweather:wght@400;700&display=swap">
<style>
  :root {
    --backdrop: #e9e9e9;
    --paper: #ffffff;
    --ink: #1f1f1f;
    --ink-soft: #3a3a3a;
    --rule: #cfcfcf;
    --brand-blue: #1f8fd0;
    --brand-green: #7bb72a;
  }
  * { box-sizing: border-box; margin: 0; padding: 0; }
  html, body {
    width: 1200px;
    height: 968px;
    overflow: hidden;
    background: var(--backdrop);
    font-family: "Merriweather", Georgia, serif;
    color: var(--ink);
  }
  .letterhead {
    position: absolute;
    left: 282px;
    top: 34px;
    width: 636px;
    height: 900px;
    background: var(--paper);
    box-shadow: 0 2px 10px rgba(0,0,0,0.08);
  }
  .brand {
    position: absolute;
    top: 44px;
    right: 48px;
    display: flex;
    align-items: center;
    gap: 8px;
  }
  .brand-dot {
    width: 12px;
    height: 12px;
    border-radius: 50%;
    background: var(--brand-blue);
  }
  .brand-name {
    font-size: 12px;
    font-weight: 700;
    color: var(--ink);
    letter-spacing: 0.02em;
  }
  .doctor {
    position: absolute;
    top: 214px;
    left: 0;
    width: 206px;
  }
  .doctor-name {
    padding-left: 34px;
    font-size: 13px;
    font-weight: 400;
    color: var(--ink);
    margin-bottom: 5px;
    white-space: nowrap;
  }
  .doctor-rule {
    display: flex;
    height: 2px;
  }
  .doctor-rule .blue { flex: 0 0 44%; background: var(--brand-blue); }
  .doctor-rule .green { flex: 1; background: var(--brand-green); }
  .contact {
    position: absolute;
    right: 48px;
    bottom: 60px;
    text-align: right;
    font-size: 8px;
    color: var(--ink-soft);
    line-height: 1.9;
  }
  .contact-line { display: flex; justify-content: flex-end; gap: 12px; }
  .contact-item { display: inline-flex; align-items: center; gap: 4px; white-space: nowrap; }
  .contact-item svg { width: 8px; height: 8px; }
  .footer-rule {
    position: absolute;
    left: 48px;
    right: 48px;
    bottom: 46px;
    height: 1px;
    background: var(--rule);
  }
</style>
</head>
<body>
  <main class="letterhead">
    <header class="brand">
      <span class="brand-dot"></span>
      <span class="brand-name">Keystone Endodontics P.C.</span>
    </header>

    <section class="doctor">
      <h1 class="doctor-name">Bertram L. Oswick DDS</h1>
      <div class="doctor-rule"><span class="blue"></span><span class="green"></span></div>
    </section>

    <footer class="contact">
      <div class="contact-line">
        <span class="contact-item">
          <svg viewBox="0 0 10 10" aria-hidden="true"><circle cx="5" cy="5" r="5" fill="#1f1f1f"/><path d="M3.3 2.6l1 1-.5.7a3 3 0 0 0 1.9 1.9l.7-.5 1 1-.7.8C4.6 7.4 2.6 5.4 2.5 3.3z" fill="#fff"/></svg>
          (716)392-5061
        </span>
        <span class="contact-item">
          <svg viewBox="0 0 10 10" aria-hidden="true"><circle cx="5" cy="5" r="5" fill="#1f1f1f"/><rect x="3" y="3.5" width="4" height="3" fill="#fff"/></svg>
          (716)392-5087
        </span>
        <span class="contact-item">
          <svg viewBox="0 0 10 10" aria-hidden="true"><circle cx="5" cy="5" r="4.4" fill="none" stroke="#1f1f1f" stroke-width="1.2"/><circle cx="5" cy="5" r="1.5" fill="none" stroke="#1f1f1f" stroke-width="1"/></svg>
          bertram@oswickroot.com
        </span>
      </div>
      <div class="contact-line">
        <span class="contact-item">
          <svg viewBox="0 0 10 10" aria-hidden="true"><circle cx="5" cy="5" r="5" fill="#1f1f1f"/><path d="M5 2a2 2 0 0 1 2 2c0 1.5-2 4-2 4S3 5.5 3 4a2 2 0 0 1 2-2z" fill="#fff"/></svg>
          2748 Tollard Avenue, Suite K, West Tollard, NY 14391
        </span>
      </div>
    </footer>
    <div class="footer-rule"></div>
  </main>
</body>
</html>
```